Laser Tattoo Removal Business Cards

We are looking for a professional business card design for a laser tattoo removal business. Ideally looking for a black business card design. The name of the business is Brightline Tattoo Removal. We place our cards at local tattoo shops so we ideally are looking for something trendy/edgy to draw both male and female clientele in.

Target Market(s)

Male/Female ages 18-60

Contact Information for Business Card

black background ideally.. hoping to stay within greys, whites and black

Font styles to use
Serif
Sans Serif

Colors
121212
a9a9a9
5c5c5c
f5f5f5
ffffff
7f7f7f
606060
848484
9d9d9d

Requirements
Must have
• Employee Info:
• Melissa Thornbury
• Chief Executive Offer
• m: 919.537.2846
• w: 919.362.4178
• f: 919.685.3907
• mthornbury@brightlinetattooremoval.example
• Address:
• 4615 Oakmere Pkwy, Suite 210
• Raleigh, NC 27654
• Website:
• www.brightlinetattooremoval.example
Nice to have
• Myabe business name on back or logo on back and employee info on the front

```html
<!DOCTYPE html>
<html lang="en">
<head>
<meta charset="utf-8">
<title>Brightline Tattoo Removal – Business Card</title>
<link rel="stylesheet" href="https://fonts.googleapis.com/css2?family=Oswald:wght@400&family=Roboto:wght@400;500;700&family=Roboto+Condensed:wght@500;700&display=swap">
<style>
  :root {
    --ink: #121212;
    --paper: #d8d8d8;
    --white: #f5f5f5;
    --text-dark: #5c5c5c;
    --text-strong: #121212;
    --rule: #7f7f7f;
    --stage: #9d9d9d;
    --card-w: 746px;
    --card-h: 428px;
  }
  * { box-sizing: border-box; margin: 0; padding: 0; }
  html, body {
    width: 1105px;
    height: 1200px;
    overflow: hidden;
  }
  body {
    background: var(--stage);
    position: relative;
    font-family: "Roboto", Arial, sans-serif;
  }
  .card {
    position: absolute;
    left: 180px;
    width: var(--card-w);
    height: var(--card-h);
    overflow: hidden;
  }
  .card--front { top: 119px; background: var(--ink); }
  .card--back  { top: 637px; background: var(--ink); }

  /* Front */
  .front__header {
    position: absolute;
    top: 0; right: 55px;
    text-align: right;
    color: var(--white);
  }
  .front__name {
    margin-top: 54px;
    font-family: "Roboto Condensed", Arial, sans-serif;
    font-weight: 700;
    font-size: 25px;
    letter-spacing: 0.3px;
    line-height: 1;
  }
  .front__title {
    margin-top: 4px;
    font-family: "Roboto Condensed", Arial, sans-serif;
    font-weight: 500;
    font-size: 18px;
    line-height: 1.1;
  }
  .front__rule {
    position: absolute;
    top: 110px;
    right: 55px;
    width: 460px;
    height: 1px;
    background: linear-gradient(to right, rgba(127,127,127,0), var(--rule));
  }
  .front__email {
    position: absolute;
    top: 118px;
    right: 55px;
    color: var(--white);
    font-size: 18px;
    line-height: 1.2;
  }
  .front__panel {
    position: absolute;
    left: 0; right: 0; bottom: 0;
    top: 190px;
    background: var(--paper);
    border-top-left-radius: 110px 44px;
  }
  .contact-numbers {
    position: absolute;
    left: 57px;
    bottom: 40px;
    list-style: none;
    font-size: 18px;
    line-height: 23px;
    color: var(--text-dark);
  }
  .contact-numbers__label {
    display: inline-block;
    width: 20px;
    font-weight: 700;
    color: var(--text-strong);
  }
  .contact-address {
    position: absolute;
    right: 55px;
    bottom: 40px;
    text-align: right;
    font-style: normal;
    font-size: 18px;
    line-height: 23px;
    color: var(--text-dark);
  }
  .contact-address__web { color: var(--text-strong); }

  /* Back */
  .back__name {
    position: absolute;
    top: 168px;
    left: 0; right: 0;
    text-align: center;
    font-family: "Oswald", "Arial Narrow", sans-serif;
    font-weight: 400;
    font-size: 40px;
    letter-spacing: 3px;
    text-transform: uppercase;
    color: var(--paper);
  }
  .back__web {
    position: absolute;
    top: 364px;
    left: 0; right: 0;
    text-align: center;
    font-size: 17px;
    letter-spacing: 3px;
    color: var(--paper);
  }
</style>
</head>
<body>

<section class="card card--front" aria-label="Business card front">
  <div class="front__panel"></div>
  <header class="front__header">
    <h1 class="front__name">MELISSA THORNBURY</h1>
    <p class="front__title">Chief Executive Offer</p>
  </header>
  <div class="front__rule"></div>
  <p class="front__email">mthornbury@brightlinetattooremoval.example</p>

  <ul class="contact-numbers">
    <li><span class="contact-numbers__label">P</span>919.362.4178</li>
    <li><span class="contact-numbers__label">C</span>919.537.2846</li>
    <li><span class="contact-numbers__label">F</span>919.685.3907</li>
  </ul>

  <address class="contact-address">
    4615 Oakmere Pkwy, Suite 210<br>
    Raleigh, NC 27654<br>
    <span class="contact-address__web">www.brightlinetattooremoval.example</span>
  </address>
</section>

<section class="card card--back" aria-label="Business card back">
  <p class="back__name">Brightline Tattoo Removal</p>
  <p class="back__web">www.brightlinetattooremoval.example</p>
</section>

</body>
</html>
```